accomplished personal trainer, former elite gymnast from Russia, highly professional and experienced

Established Fitness trainer in California requires a new web site to attract personal clients and build her group exercise classes.

Here is an example of another fitness trainer's site that I really liked the technology:
http://www.tedvorlam.com

Below I have inserted my current web site: www.quelbornfitnesslodi.com
You can use this web site for the principal content, such as my background and qualifications.

Target Market(s)

Anyone who wants to improve their fitness levels and wellness in general. Anyone who needs directions and instruction on how to exercise. I can train anyone from elite athlete to a disabled person.

Industry/Entity Type

Fitness

Coding

Coded - Design and coding required

Number of Pages Required

5+ page

Font styles to use
Sans Serif

Requirements
Must have
• Easy to navigate main info about me, location, services, contact, benefits of using my services.
• Would be great to create unique representation of me as a trainer and a person, using new technologies and new ideas. Make it different from the other websites. Having its own character. Not too complicated and heavy with information, but an eye catching, useful and fun to navigate.
Nice to have
• new technology, easy access to information, the idea of enjoyment of life, lightness about achieving any goal, spiritual wisdom, unique design. I am planning to insert educational videos, advise, maybe jokes. Sign in, shopping cart, logo, should be easy for me to make changes in content.
Should not have
• cliché, outdated technology, too complicated,

```html
<!DOCTYPE html>
<html lang="en">
<head>
<meta charset="utf-8">
<title>Quelborn Fitness Lodi</title>
<link href="https://fonts.googleapis.com/css2?family=Ubuntu:wght@400;500;700&family=Open+Sans:wght@400;600;700&display=swap" rel="stylesheet">
<style>
:root{
  --green:#3db706;
  --green-dark:#2f9a03;
  --ink:#2a2a2a;
  --text:#4a4a4a;
  --muted:#777;
  --dark:#1f2322;
  --white:#fff;
  --diamond:#e6e6e6;
  --diamond-dot:#9a9a9a;
  --role:#d44a4a;
}
*{margin:0;padding:0;box-sizing:border-box}
html,body{width:1200px;height:3704px;overflow:hidden}
body{position:relative;background:var(--white);font-family:"Open Sans",Arial,sans-serif;color:var(--text)}
h1,h2,h3{font-family:"Ubuntu",Arial,sans-serif;font-weight:500;color:var(--ink)}
.section-title{position:absolute;left:0;width:1200px;text-align:center;font-size:33px;letter-spacing:1px;text-transform:uppercase}
.title-rule{position:absolute;height:3px;width:170px;background:var(--green)}

/* header */
.site-header{position:absolute;left:0;top:0;width:1200px;height:80px;background:var(--white)}
.brand{position:absolute;left:49px;top:24px;font-family:"Ubuntu",Arial,sans-serif;font-size:30px;font-weight:500;color:var(--ink);letter-spacing:1px}
.main-nav{position:absolute;right:38px;top:35px;display:flex}
.main-nav a{font-size:14px;color:var(--ink);text-decoration:none;text-transform:uppercase;margin-left:58px}

/* hero */
.hero{position:absolute;left:0;top:80px;width:1200px;height:557px;background:linear-gradient(180deg,#8fb35a 0%,#b8cf8a 30%,#7fa44a 60%,#5e8c2c 100%)}
.hero-box{position:absolute;left:365px;top:243px;width:494px;height:118px;background:rgba(20,20,20,.55);text-align:center}
.hero-box h1{font-weight:400;color:var(--white);font-size:40px;letter-spacing:1px;margin-top:8px}
.hero-btn{position:absolute;left:158px;top:74px;width:168px;height:38px;border:1px solid var(--white);color:var(--white);font-size:14px;line-height:36px;text-transform:uppercase}

/* exercise */
.exercise-photo{position:absolute;left:37px;top:716px;width:408px;height:346px;background:linear-gradient(180deg,#f3f3f3,#d9c2ad 55%,#3a3a3a)}
.exercise-copy{position:absolute;left:454px;top:755px;width:690px;font-size:15px;line-height:22px}
.exercise-copy p{margin-bottom:20px}
.exercise-copy strong{display:block;color:var(--ink);margin-bottom:14px}
.cert-list{list-style:none}
.cert-list li{position:relative;padding-left:20px;line-height:20px}
.cert-list li::before{content:"";position:absolute;left:2px;top:6px;border-left:7px solid var(--green);border-top:4px solid transparent;border-bottom:4px solid transparent}

/* why */
.why-photo{position:absolute;left:0;top:1062px;width:568px;height:449px;background:linear-gradient(160deg,#4d6b2e,#7a9a4f 45%,#a7c07a 75%,#cfd9b7)}
.why-panel{position:absolute;left:568px;top:1062px;width:632px;height:449px;background:var(--green);color:var(--white)}
.why-panel h2{position:absolute;left:20px;top:20px;color:var(--white);font-weight:400;font-size:38px;line-height:44px;text-transform:uppercase;letter-spacing:1px}
.why-panel h2 small{font-size:28px}
.why-intro{position:absolute;left:26px;top:110px;width:580px;font-size:15px;line-height:22px}
.benefit{position:absolute;left:34px;width:470px}
.benefit h3{color:var(--white);font-family:"Open Sans",Arial,sans-serif;font-weight:700;font-size:14px}
.benefit p{font-size:12.5px;line-height:19px}
.benefit-icon{position:absolute;width:50px;height:50px;border-radius:50%;background:var(--white);border:3px solid var(--green)}
.benefit-icon svg{position:absolute;left:11px;top:11px}

/* trainers */
.trainer{position:absolute;top:1647px;width:341px;height:440px;text-align:center}
.trainer-photo{width:341px;height:341px}
.trainer-social{position:absolute;left:37px;top:279px;width:267px;height:62px;background:var(--white);display:flex;justify-content:center;align-items:center;gap:30px}
.trainer-social span{position:relative;display:block;width:28px;height:28px;background:var(--diamond);transform:rotate(45deg)}
.trainer-social span::after{content:"";position:absolute;left:11px;top:11px;width:6px;height:6px;border-radius:50%;background:var(--diamond-dot)}
.trainer-role{position:absolute;left:0;width:341px;top:383px;font-size:12px;color:var(--role)}
.trainer-name{position:absolute;left:0;width:341px;top:408px;font-size:14px;color:#555;text-transform:uppercase;font-family:"Times New Roman",serif}

/* motto */
.motto{position:absolute;left:0;top:2136px;width:1200px;height:437px;background:linear-gradient(180deg,#262b29,#353b37 50%,#202423);text-align:center;color:var(--white)}
.motto h2{color:var(--white);font-weight:400;font-size:32px;margin-top:44px;letter-spacing:2px}
.motto .tagline{font-size:17px;margin-top:38px}
.motto .motto-text{width:960px;margin:28px auto 0;font-size:15px;line-height:25px}
.btn-green{display:inline-block;background:var(--green);color:var(--white);text-transform:uppercase;font-size:15px}
.motto .btn-green{position:absolute;left:496px;top:313px;width:210px;height:50px;line-height:50px}

/* testimonial */
.quote-mark{position:absolute;left:62px;top:2730px;font-family:"Ubuntu",sans-serif;font-size:110px;line-height:1;color:var(--green);font-weight:700}
.testimonial-text{position:absolute;left:64px;top:2810px;width:500px;font-size:15px;line-height:23px}
.testimonial-author{position:absolute;left:64px;top:2987px;font-size:15px;color:var(--green)}
.testimonial-photo{position:absolute;left:593px;top:2703px;width:567px;height:457px;background:linear-gradient(180deg,#f4f4f4,#e4d0bf 45%,#f1f1f1)}

/* contact */
.contact{position:absolute;left:0;top:3160px;width:1200px;height:487px;background:linear-gradient(180deg,#2a302e,#1c201f);color:var(--white)}
.contact h2{position:absolute;left:0;width:1200px;top:44px;text-align:center;color:var(--white);font-weight:700;font-size:35px}
.contact .sub{position:absolute;left:0;width:1200px;top:92px;text-align:center;font-size:15px}
.info-label{position:absolute;left:79px;font-size:12px;font-weight:700;text-transform:uppercase}
.info-value{position:absolute;left:333px;font-size:12px;line-height:19px;font-weight:600}
.field{position:absolute;border:1px solid #4a504e;background:rgba(255,255,255,.04);font-size:12px;color:#aaa;padding:10px 12px}
.send-btn{position:absolute;left:632px;top:366px;width:506px;height:54px;background:var(--green);color:var(--white);text-align:center;line-height:54px;font-weight:700;font-size:16px}

.site-footer{position:absolute;left:0;top:3647px;width:1200px;height:57px;background:var(--green);color:var(--white);text-align:center;font-size:15px;line-height:57px}
</style>
</head>
<body>

<header class="site-header">
  <div class="brand">QUELBORN FITNESS LODI</div>
  <nav class="main-nav">
    <a>Home</a><a>About me</a><a>Location</a><a>Services</a><a>Contact,</a>
  </nav>
</header>

<section class="hero" role="img" aria-label="Group of people doing squats outdoors on a park lawn">
  <div class="hero-box">
    <h1>FITNESS OUTDOORS</h1>
    <div class="hero-btn">Contact us</div>
  </div>
</section>

<section class="exercise">
  <h2 class="section-title" style="top:674px">Exercise Training</h2>
  <div class="title-rule" style="left:515px;top:726px"></div>
  <div class="exercise-photo" role="img" aria-label="Muscular trainer lifting a barbell"></div>
  <div class="exercise-copy">
    <p>Mira Valenko is the owner of Quelborn Fitness. She was born and raised in Vologda, Russia where she was a competitive gymnast. Mira graduated from Northvale Academy of Sport with a bachelor degree in Kinesiology and Sports Science.</p>
    <p>For more than 20 years, Mira has worked as choreographer, gymnastics coach, and fitness professional.</p>
    <strong>Certified by NFC as a</strong>
    <ul class="cert-list">
      <li>Personal Trainer</li>
      <li>Group Exercise Instructor</li>
      <li>Medical Exercise Specialist</li>
      <li>Orthopedic Exercise Specialist</li>
    </ul>
  </div>
</section>

<section class="why">
  <div class="why-photo" role="img" aria-label="Woman stretching in a split on the grass outdoors"></div>
  <div class="why-panel">
    <h2>Why<br>Choose <small>Quelborn</small></h2>
    <p class="why-intro">Mira Valenko is the owner of Quelborn Fitness. She was born and raised in Vologda, Russia where she was a competitive gymnast.</p>
    <div class="benefit" style="top:178px"><h3>Professional Trainer</h3><p>Mira Valenko is the owner of Quelborn Fitness. She was born and raised in Vologda, Russia where she was a competitive gymnast.</p></div>
    <div class="benefit" style="top:260px"><h3>Exclusive Accessories</h3><p>Mira Valenko is the owner of Quelborn Fitness. She was born and raised in Vologda, Russia where she was a competitive gymnast.</p></div>
    <div class="benefit" style="top:340px"><h3>Money Back Guarrantee</h3><p>Mira Valenko is the owner of Quelborn Fitness. She was born and raised in Vologda, Russia where she was a competitive gymnast.</p></div>
  </div>
  <div class="benefit-icon" style="top:1244px;left:541px"><svg width="22" height="22" viewBox="0 0 22 22"><circle cx="11" cy="7" r="5" fill="#3db706"/><path d="M2 21c0-6 4-8 9-8s9 2 9 8z" fill="#3db706"/></svg></div>
  <div class="benefit-icon" style="top:1326px;left:541px"><svg width="22" height="22" viewBox="0 0 22 22"><circle cx="11" cy="15" r="5" fill="#3db706"/><circle cx="4" cy="9" r="2.5" fill="#3db706"/><circle cx="8.5" cy="4" r="2.5" fill="#3db706"/><circle cx="13.5" cy="4" r="2.5" fill="#3db706"/><circle cx="18" cy="9" r="2.5" fill="#3db706"/></svg></div>
  <div class="benefit-icon" style="top:1407px;left:541px"><svg width="22" height="22" viewBox="0 0 22 22"><text x="11" y="19" text-anchor="middle" font-family="Open Sans,sans-serif" font-weight="700" font-size="20" fill="#3db706">$</text></svg></div>
</section>

<section class="trainers">
  <h2 class="section-title" style="top:1562px">World Best Trainers</h2>
  <div class="title-rule" style="left:515px;top:1612px"></div>
  <article class="trainer" style="left:67px">
    <div class="trainer-photo" role="img" aria-label="Portrait of a female personal trainer in a gym" style="background:linear-gradient(160deg,#e9b98a,#b58464 50%,#6c4f86)"></div>
    <div class="trainer-social"><span></span><span></span><span></span></div>
    <div class="trainer-role">Personal Trainer</div>
    <div class="trainer-name">Rena Holloway</div>
  </article>
  <article class="trainer" style="left:437px">
    <div class="trainer-photo" role="img" aria-label="Portrait of a male pilates trainer with a towel" style="background:linear-gradient(160deg,#8a6f5a,#c9a48a 45%,#d8dde2)"></div>
    <div class="trainer-social"><span></span><span></span><span></span></div>
    <div class="trainer-role">Pilates Trainers</div>
    <div class="trainer-name">Marco Delane</div>
  </article>
  <article class="trainer" style="left:805px">
    <div class="trainer-photo" role="img" aria-label="Portrait of a female weight trainer seated in a gym" style="background:linear-gradient(160deg,#d9d4cf,#a8836c 45%,#3a3a3e)"></div>
    <div class="trainer-social"><span></span><span></span><span></span></div>
    <div class="trainer-role">Weight Trainer</div>
    <div class="trainer-name">Tessa Orwin</div>
  </article>
</section>

<section class="motto" aria-label="Dark background of people running in a park">
  <h2>HEALTHY MIND, HEALTHY BODY</h2>
  <p class="tagline">"Give your life some new energy."</p>
  <p class="motto-text">You have the opportunity today to learn, to grow, to achieve and to experience new things. To do so youthe courage to let go of some old, comfortable, predictable things. A wonderful sereny has taken possessoul, like these sweet mornings of spring. Duis aute irure dolor in reprehendet in voluptate velit esse cillu. A wonderful sereny has taken possession of my entire soul.</p>
  <span class="btn-green">Get membership now</span>
</section>

<section class="testimonials">
  <h2 class="section-title" style="top:2620px">What Our Happy Clients Says</h2>
  <div class="title-rule" style="left:515px;top:2668px"></div>
  <div class="quote-mark">&ldquo;</div>
  <p class="testimonial-text">Nullam porttitor lacus a lorem consectetur aliquet. Aenean rutrum augue mauris. Cras elit nibh, malesuada eget sodales non, dignissim eget elit. Quisque lectus mi, posuere non elit nec, imperdiet pulvinar leo. Curabitur semper id massa id pulvinar. Mauris laoreet mollis tortor. Morbi ac nulla in nibh tempor pharetra. Curabitur commodo, enim at fermentum convallis,</p>
  <div class="testimonial-author">- Lena Marsh</div>
  <div class="testimonial-photo" role="img" aria-label="Woman in sportswear stretching on the floor"></div>
</section>

<section class="contact">
  <h2>GET IN TOUCH</h2>
  <p class="sub">Have a question for us?</p>
  <div class="info-label" style="top:172px">Operating hours:</div>
  <div class="info-value" style="top:170px">Monday to Friday 10:00 to 23:00.<br>Saturdays 12:00 to 00:00.<br>Sundays 14:00 to 22:00.</div>
  <div class="info-value" style="top:236px">Closed on public holidays.</div>
  <div class="info-label" style="top:280px">Address:</div>
  <div class="info-value" style="top:278px">218 Orchard Lane, Lodi,<br>CA 95240</div>
  <div class="info-label" style="top:337px">Telephone:</div>
  <div class="info-value" style="top:335px">+1 209 555 0148</div>
  <div class="info-label" style="top:377px">Fax:</div>
  <div class="info-value" style="top:375px">+1 209 555 0149</div>
  <div class="info-label" style="top:413px">Email:</div>
  <div class="info-value" style="top:411px">hello@quelbornfitness.com</div>

  <div class="field" style="left:632px;top:156px;width:170px;height:44px">Name *</div>
  <div class="field" style="left:820px;top:156px;width:150px;height:44px">Email *</div>
  <div class="field" style="left:988px;top:156px;width:150px;height:44px">Subject *</div>
  <div class="field" style="left:632px;top:220px;width:506px;height:126px">Message *</div>
  <div class="send-btn">Send Message</div>
</section>

<footer class="site-footer">&copy; copyright 2016, All Rights Reserved &nbsp;Privacy Policy | Terms and Conditions</footer>

</body>
</html>
```